Business Card for a Creative Technology based HR services company

Our company name is Lumo8, and we build large communities of HR (human resource) and finance personnels through our mobile platform, and we conduct lots of on-line and off-line activities to get everyone constantly connected. Behind all these, we will also provide on-site HR and finance contractors to our clients, plus a host of other HR-related services. No process in our company takes more than 5-steps.
Our company slogan: Touching Your Future
Target Market(s)
All human resource (HR) and finance personnels, from new entrants to highly experienced senior professionals.
Industry/Entity Type
Finance
Colors
Designer to choose colors to be used in the design.
Look and feel
Each slider illustrates characteristics of the customer's brand and the style your logo design should communicate.

```html
<!DOCTYPE html>
<html lang="en">
<head>
<meta charset="utf-8">
<title>Lumo8 Business Card</title>
<link rel="stylesheet" href="https://fonts.googleapis.com/css2?family=Open+Sans:wght@400;600;700&display=swap">
<style>
  :root {
    --page-bg: #e6e8ec;
    --card-white: #ffffff;
    --brand-navy: #14315c;
    --brand-red: #e3141f;
    --text-light: #ffffff;
    --card-shadow: rgba(20, 30, 50, 0.18);
  }
  * { margin: 0; padding: 0; box-sizing: border-box; }
  html, body {
    width: 1200px;
    height: 901px;
    overflow: hidden;
    background: var(--page-bg);
    font-family: "Open Sans", Arial, sans-serif;
  }
  .stage {
    position: relative;
    width: 1200px;
    height: 901px;
  }
  .card {
    position: absolute;
    left: 250px;
    width: 700px;
    height: 400px;
    border-radius: 42px;
    background: var(--card-white);
    overflow: hidden;
    box-shadow: 0 10px 30px var(--card-shadow);
  }
  .card--front { top: 30px; }
  .card--back { top: 470px; }
  .card__art {
    position: absolute;
    inset: 0;
    width: 100%;
    height: 100%;
  }
  .navy-panel { fill: var(--brand-navy); }
  .red-arc { fill: var(--brand-red); }
  .contact {
    position: absolute;
    left: 42px;
    top: 48px;
    color: var(--text-light);
  }
  .contact__name {
    font-size: 21px;
    font-weight: 700;
    line-height: 1.2;
  }
  .contact__role {
    font-size: 20px;
    font-weight: 400;
    line-height: 1.2;
  }
  .contact__address {
    margin-top: 46px;
    font-size: 17px;
    line-height: 1.35;
  }
  .contact__lines {
    margin-top: 40px;
    list-style: none;
    font-size: 17px;
    line-height: 1.3;
  }
  .contact__lines li {
    display: flex;
    align-items: center;
    gap: 7px;
  }
  .contact__icon {
    width: 13px;
    height: 13px;
    fill: var(--text-light);
    flex: none;
  }
  .contact__web {
    font-size: 17px;
    line-height: 1.3;
  }
  .brand {
    position: absolute;
    display: flex;
    align-items: center;
    gap: 8px;
    color: var(--brand-navy);
    font-weight: 700;
    letter-spacing: -1px;
  }
  .brand__dot {
    width: 0.62em;
    height: 0.62em;
    border-radius: 50%;
    background: var(--brand-red);
  }
  .card--front .brand {
    left: 440px;
    top: 158px;
    font-size: 62px;
  }
  .card--back .brand {
    left: 50%;
    top: 40px;
    transform: translateX(-50%);
    font-size: 56px;
  }
</style>
</head>
<body>
<main class="stage">

  <section class="card card--front" aria-label="Business card front">
    <svg class="card__art" viewBox="0 0 700 400" aria-hidden="true">
      <path class="navy-panel" d="M0 0 H300 C392 110 392 290 300 400 H0 Z"/>
      <path class="red-arc" d="M312 0 C404 110 404 290 312 400 H330 C424 290 424 110 338 0 Z"/>
    </svg>

    <div class="contact">
      <p class="contact__name">Maren Colby-Hale</p>
      <p class="contact__role">Consultant</p>
      <p class="contact__address">041.12th floor,Park<br>Ridgeway Road LKG</p>
      <ul class="contact__lines">
        <li>
          <svg class="contact__icon" viewBox="0 0 16 16" aria-hidden="true"><path d="M3 1 L6 1 L7 5 L5 6.5 C6 9 7 10 9.5 11 L11 9 L15 10 L15 13 C15 14 14 15 13 15 C6 15 1 10 1 3 C1 2 2 1 3 1 Z"/></svg>
          <span>012 555 0198</span>
        </li>
        <li>
          <svg class="contact__icon" viewBox="0 0 16 16" aria-hidden="true"><path d="M4 1 H11 V5 H4 Z M2 6 H14 V14 H2 Z"/></svg>
          <span>012 555 0198</span>
        </li>
        <li>
          <svg class="contact__icon" viewBox="0 0 16 16" aria-hidden="true"><path d="M1 3 H15 V13 H1 Z M1 3 L8 9 L15 3" stroke="#14315c" stroke-width="1.2"/></svg>
          <span>hello@lumo8mail.com</span>
        </li>
      </ul>
      <p class="contact__web">www.lumo8hrplatform.com</p>
    </div>

    <div class="brand"><span>Lumo8</span><span class="brand__dot"></span></div>
  </section>

  <section class="card card--back" aria-label="Business card back">
    <div class="brand"><span>Lumo8</span><span class="brand__dot"></span></div>
  </section>

</main>
</body>
</html>
```